National online rug retailer needs a home page design

See the FloorNest logo and create a home page design around that color theme. Details are spelled out in word document uploaded below.

Apparently this website did not take my attachement showing the logo and basic requirements.  If you would send me your email address, I will send you the attachment directly.
Best regards,
Tom Vance
tvance@mrdcorp.example

Target Market(s)

The target market is home owners 25 to 75 years old with combined incomes over $100,000 per year.

Industry/Entity Type

Online

Requirements
Must have
• Lots of white space with black letters and creative use of red and possibly one other color. Would like a compelling call to action button.

```html
<!DOCTYPE html>
<html lang="en">
<head>
<meta charset="utf-8">
<title>FloorNest – Home</title>
<link href="https://fonts.googleapis.com/css2?family=Open+Sans:wght@400;600;700&family=PT+Sans+Narrow&display=swap" rel="stylesheet">
<style>
:root{
  --red:#c8102e;
  --red-dark:#9e0f1f;
  --crimson:#9a1f4b;
  --ink:#222;
  --muted:#555;
  --line:#d9d9d9;
  --panel:#f2f2f2;
  --slate:#3d3f42;
  --footer-bar:#3a3a3a;
}
*{margin:0;padding:0;box-sizing:border-box}
html,body{width:746px;height:1200px;overflow:hidden;background:#fff}
body{position:relative;font-family:"Open Sans",Arial,sans-serif;color:var(--ink)}
.abs{position:absolute}

/* header */
.brand{left:80px;top:12px;display:flex;align-items:center;gap:6px}
.brand-mark{width:18px;height:18px;background:var(--red)}
.brand-name{font-size:25px;font-weight:600;color:var(--red);letter-spacing:-.5px}
.tagline{left:136px;top:49px;font-size:7.5px;color:var(--muted)}
.search{left:289px;top:37px;display:flex;gap:2px}
.search-input{width:141px;height:15px;border:1px solid #888;background:#fff}
.search-btn{width:38px;height:15px;background:#4a4a4a;color:#fff;font-size:10px;text-align:center;line-height:15px}
.cart-line{left:503px;top:11px;font-size:7.5px;color:var(--muted)}
.cart-line b{color:var(--ink);font-weight:600}
.phone-line{left:502px;top:25px;font-size:10px;color:var(--muted)}
.phone-line span{color:var(--red);font-weight:600;margin-left:4px}
.account-line{left:503px;top:42px;font-size:7.5px;color:var(--muted);display:flex;gap:7px;align-items:center}

/* nav */
.nav{left:0;top:70px;width:746px;height:25px;background:linear-gradient(#b80f22,var(--red-dark));border-top:1px solid #7e0a16;display:flex;align-items:center;padding-left:72px}
.nav a{color:#fff;font-size:9px;text-decoration:none;padding:0 21px;border-right:1px solid rgba(255,255,255,.45);line-height:12px}
.nav a:last-child{border-right:none}

/* hero */
.filter-menu{left:68px;top:108px;width:150px}
.filter-menu li{list-style:none;height:29.3px;line-height:29px;padding-left:10px;font-size:9.5px;background:linear-gradient(90deg,#fff,#f1f1f1);border-bottom:2px solid #e3e3e3;border-right:2px solid #e3e3e3}
.filter-active{left:68px;top:108px;height:29px;width:184px}
.hero-img{left:218px;top:108px;width:460px;height:236px;background:linear-gradient(120deg,#8a6a4a 0%,#c59a6a 40%,#e8d7b8 60%,#9c7b58 100%)}
.hero-caption{left:218px;top:285px;width:202px;height:59px;background:rgba(40,40,40,.85);color:#fff;font-family:"PT Sans Narrow",sans-serif;font-size:25px;line-height:25px;padding:5px 12px}

/* categories */
.cat-img{top:371px;height:101px}
.cat-label{top:474px;height:29px;color:#fff;font-size:16px;text-align:center;line-height:29px;background:var(--slate);border:1px solid #222}

/* section headings */
.sec-title{font-size:12.5px;color:#333;letter-spacing:.2px}
.arrow{width:12px;height:12px}

/* product cards */
.card{width:167px;height:180px;border:1px solid var(--line);box-shadow:0 1px 2px rgba(0,0,0,.12);background:#fff}
.card-img{position:absolute;left:8px;top:8px;width:150px;height:114px}
.card-rule{position:absolute;left:0;top:134px;width:100%;border-top:1px dotted #aaa}
.card-rule::before{content:"";position:absolute;left:0;top:-2px;width:18px;height:3px;background:var(--red-dark)}
.price{position:absolute;left:5px;top:149px;font-size:7.5px}
.price s{color:#777;margin-right:6px}
.price span{color:var(--red)}
.cart-btn{position:absolute;left:110px;top:145px;width:50px;height:15px;background:var(--red-dark);color:#fff;font-size:5.5px;font-weight:700;text-align:center;line-height:15px;border-radius:2px;box-shadow:0 1px 1px rgba(0,0,0,.4)}

/* you may also like */
.ymal{left:460px;top:558px;width:218px;height:381px;border:1px solid var(--line);box-shadow:0 1px 2px rgba(0,0,0,.12)}
.ymal-img{left:11px;width:196px;height:143px}
.ymal-label{left:11px;width:196px;height:28px;background:var(--slate);color:#fff;font-size:15px;text-align:center;line-height:28px}

/* footer */
.footer{left:70px;top:965px;width:608px;height:201px;background:var(--panel)}
.foot-col{top:19px}
.foot-col h4{font-size:8.5px;font-weight:600;color:#333;margin-bottom:20px}
.foot-col li{list-style:none;font-size:7.5px;color:#444;line-height:12.4px}
.foot-rule{left:14px;top:38px;width:578px;border-top:1px solid #ddd}
.pay{height:14px;width:21px;border-radius:2px}
.seal{height:22px}
.bottom-bar{left:0;top:1166px;width:746px;height:34px;background:var(--footer-bar);color:#aaa;font-size:7.5px;text-align:center;line-height:34px}
</style>
</head>
<body>

<header>
  <div class="abs brand"><div class="brand-mark"></div><div class="brand-name">FloorNest.com</div></div>
  <div class="abs tagline">for domestic and heirloom values</div>
  <div class="abs search"><div class="search-input"></div><div class="search-btn">Search</div></div>
  <div class="abs cart-line">Items (0) &nbsp;<b>Total $0.00</b> &nbsp;View Cart &nbsp;|&nbsp; Checkout</div>
  <div class="abs phone-line">Order Toll-Free &nbsp;: <span>1-888-555-0142</span></div>
  <div class="abs account-line">
    <span>My Account &nbsp;| &nbsp;Sign</span>
    <span><svg width="7" height="7" viewBox="0 0 10 10"><path d="M1 1h8v6H4l-3 2z" fill="#333"/></svg> Live Chat</span>
    <span><svg width="7" height="7" viewBox="0 0 10 10"><circle cx="5" cy="3" r="2.4" fill="#333"/><path d="M0 10c0-4 10-4 10 0z" fill="#333"/></svg> Online</span>
  </div>
</header>

<nav class="abs nav">
  <a>Home</a><a>Selection guides</a><a>Rug Care</a><a>FAQ</a><a>Return Policy</a><a>Free Shipping</a><a>Clearance Rugs</a>
</nav>

<section>
  <ul class="abs filter-menu">
    <li style="background:transparent;border:none">&nbsp;</li>
    <li>COLOR WAY</li><li>SIZE</li><li>SHAPE</li><li>FIBER CONTENT</li><li>MFGR. BRAND</li><li>MFGR.COLLECTION</li><li>PRICE</li>
  </ul>
  <svg class="abs filter-active" viewBox="0 0 184 29"><defs><linearGradient id="fg" x1="0" x2="1"><stop offset="0" stop-color="#d6d6d6"/><stop offset="1" stop-color="#c4c4c4"/></linearGradient></defs><path d="M0 0H166L184 14.5 166 29H0z" fill="url(#fg)"/><text x="10" y="19" font-family="Open Sans, sans-serif" font-size="9.5" fill="#222">RUG THEME</text></svg>
  <div class="abs hero-img" role="img" aria-label="Living room with cream sectional sofa, yellow cushions and a wood coffee table on a rug"></div>
  <div class="abs hero-caption">For Domestic and Heirloom values</div>
</section>

<section>
  <div class="abs cat-img" style="left:68px;width:197px;background:linear-gradient(#4a3a2c,#e8e2d8 55%,#f4f1ea)" role="img" aria-label="Shag rug under a dark wood coffee table"></div>
  <div class="abs cat-img" style="left:273px;width:200px;background:linear-gradient(#d8dccf,#f2f2ea 50%,#e6e4d6)" role="img" aria-label="White shag rug beside a cream sofa"></div>
  <div class="abs cat-img" style="left:479px;width:199px;background:linear-gradient(#d8dccf,#f2f2ea 50%,#e6e4d6)" role="img" aria-label="White shag rug beside a cream sofa"></div>
  <div class="abs cat-label" style="left:68px;width:204px">Tradional</div>
  <div class="abs cat-label" style="left:272px;width:203px;background:var(--crimson)">Transitional</div>
  <div class="abs cat-label" style="left:475px;width:203px">Casual</div>
</section>

<section>
  <div class="abs sec-title" style="left:70px;top:525px">FEATURED PRODUCTS</div>
  <svg class="abs arrow" style="left:386px;top:527px" viewBox="0 0 12 12"><circle cx="6" cy="6" r="6" fill="#999"/><path d="M7.5 3L4 6l3.5 3z" fill="#fff"/></svg>
  <svg class="abs arrow" style="left:403px;top:527px" viewBox="0 0 12 12"><circle cx="6" cy="6" r="6" fill="#222"/><path d="M4.5 3L8 6 4.5 9z" fill="#fff"/></svg>

  <div class="abs card" style="left:70px;top:558px"><div class="card-img" style="background:linear-gradient(135deg,#6b1a14,#efe6d2 30%,#efe6d2 70%,#6b1a14)" role="img" aria-label="Bordered rug with card-suit motifs"></div><div class="card-rule"></div><div class="price"><s>$55.67</s><span>$48.67</span></div><div class="cart-btn">ADD TO CART</div></div>
  <div class="abs card" style="left:254px;top:558px"><div class="card-img" style="background:linear-gradient(#e4e4e4,#bdbdbd 60%,#8d8d8d)" role="img" aria-label="Grey geometric rug in a modern room"></div><div class="card-rule"></div><div class="price"><s>$55.67</s><span>$48.67</span></div><div class="cart-btn">ADD TO CART</div></div>
  <div class="abs card" style="left:70px;top:760px"><div class="card-img" style="background:linear-gradient(#e9dcc7,#a31a1a 45%,#8a1414 85%,#c89a5e)" role="img" aria-label="Red rug with swirl lines on a wood floor"></div><div class="card-rule"></div><div class="price"><s>$55.67</s><span>$48.67</span></div><div class="cart-btn">ADD TO CART</div></div>
  <div class="abs card" style="left:254px;top:760px"><div class="card-img" style="background:linear-gradient(135deg,#2a1c16,#4a2e22 50%,#2a1c16)" role="img" aria-label="Dark rug with colourful circle pattern"></div><div class="card-rule"></div><div class="price"><s>$55.67</s><span>$48.67</span></div><div class="cart-btn">ADD TO CART</div></div>

  <div class="abs sec-title" style="left:460px;top:525px">YOU MAY ALSO LIKE</div>
  <svg class="abs arrow" style="left:649px;top:527px" viewBox="0 0 12 12"><circle cx="6" cy="6" r="6" fill="#999"/><path d="M7.5 3L4 6l3.5 3z" fill="#fff"/></svg>
  <svg class="abs arrow" style="left:666px;top:527px" viewBox="0 0 12 12"><circle cx="6" cy="6" r="6" fill="#222"/><path d="M4.5 3L8 6 4.5 9z" fill="#fff"/></svg>

  <div class="abs ymal">
    <div class="abs ymal-img" style="top:12px;background:linear-gradient(#ece8e0,#c08a4e 45%,#1f2438 60%,#8a4a2a 80%,#c58e52)" role="img" aria-label="Navy and rust patterned rug on a wood floor"></div>
    <div class="abs ymal-label" style="top:155px">Cool &amp; Calming</div>
    <div class="abs ymal-img" style="top:198px;background:linear-gradient(#ddd,#b3141c 35%,#e8e4df 60%,#8c1a1a)" role="img" aria-label="Red and white swirl shag rug before a red sofa"></div>
    <div class="abs ymal-label" style="top:340px">Natural Rugs</div>
  </div>
</section>

<footer class="abs footer">
  <div class="abs foot-col" style="left:14px"><h4>Customer Services</h4><ul><li>Shipping</li><li>Return Policy</li><li>Privacy Policy</li><li>Ordering &amp; Delivery</li><li>Checklist</li><li>Terms of Use</li><li>Terms of Sale</li><li>Contact Us</li><li>Environmental Policy</li></ul></div>
  <div class="abs foot-col" style="left:140px"><h4>Resources</h4><ul><li>Product Articles</li><li>Learning Center</li><li>Help</li><li>Refer A Friend</li><li>FloorNest Blog</li><li>Room Scene Viewer</li><li>Site Map</li><li>FAQ</li><li>Customer Testimonials</li><li>Photo Gallery</li></ul></div>
  <div class="abs foot-col" style="left:258px"><h4>Corporate Info</h4><ul><li>About FloorNest.com</li><li>Careers</li><li>Affiliates</li></ul></div>
  <div class="abs foot-col" style="left:386px"><h4>Payments &amp; Security</h4></div>
  <div class="abs foot-rule"></div>
  <div class="abs" style="left:386px;top:55px;display:flex;gap:3px;align-items:center">
    <div class="pay" style="background:#2a3f8f"></div><div class="pay" style="background:#e7e7e7;border:1px solid #ccc"></div><div class="pay" style="background:#1a3d8f"></div><div class="pay" style="background:#4a8fd0"></div><div class="pay" style="background:#e8b13a"></div>
    <div style="width:82px;height:22px;background:#1c4a8a;border-radius:2px;margin-left:2px"></div>
  </div>
  <div class="abs" style="left:384px;top:92px;display:flex;gap:4px;align-items:center">
    <div class="seal" style="width:30px;border-radius:50%;background:#d7b93a"></div>
    <div class="seal" style="width:30px;border-radius:50%;background:#c9a92c"></div>
    <div class="seal" style="width:40px;background:#a31621;border-radius:2px"></div>
    <div class="seal" style="width:44px;background:#1f4f8a;border-radius:2px"></div>
    <div class="seal" style="width:48px;background:#3e3e3e;border-radius:2px"></div>
  </div>
</footer>
<div class="abs bottom-bar">© Copyrights 2013 &nbsp;FloorNest. All rights Reserved</div>

</body>
</html>
```